Northfield Builders Guild Business card

We are looking for a new business card design with photo included.
Our business is a nonprofit construction contractor membership organization. We offer business education, assist with business setup and licensing, provide safety training, and provide a member directory.
URL: www.builderslinkguild.org
Color code:
CMYK: 0 cyan, 42 magenta, 100 yellow, 0 black for Print.
Hexidecimal: #FF9900
RGB: R 255; G 153; B 0

```html
<!DOCTYPE html>
<html lang="en">
<head>
<meta charset="utf-8">
<title>Northfield Builders Guild – Business Card</title>
<link href="https://fonts.googleapis.com/css2?family=Source+Sans+3:wght@400;600;700&display=swap" rel="stylesheet">
<style>
  :root {
    --bg: #d0d0d0;
    --charcoal: #3b3b3c;
    --charcoal-light: #4a4a4b;
    --orange: #f5a623;
    --paper: #f7f7f7;
    --ink: #2e2e2e;
    --muted: #e9e9e9;
  }
  * { margin: 0; padding: 0; box-sizing: border-box; }
  html, body { width: 1200px; height: 800px; overflow: hidden; }
  body {
    background: var(--bg);
    font-family: "Source Sans 3", sans-serif;
    position: relative;
  }
  .card {
    position: absolute;
    width: 530px;
    height: 303px;
    top: 248px;
    box-shadow: 0 4px 14px rgba(0,0,0,0.18);
    overflow: hidden;
  }
  /* Back of card */
  .card--back {
    left: 52px;
    background: linear-gradient(135deg, var(--charcoal) 0%, var(--charcoal-light) 100%);
    color: #fff;
  }
  .back-brand {
    position: absolute;
    left: 0; right: 0; top: 92px;
    display: flex;
    align-items: center;
    justify-content: center;
    gap: 12px;
  }
  .brand-mark {
    width: 14px; height: 14px;
    background: var(--orange);
  }
  .brand-name {
    font-weight: 700;
    font-size: 34px;
    letter-spacing: 0.5px;
    line-height: 1;
  }
  .card--back .brand-name { color: #fff; }
  .services {
    position: absolute;
    left: 0; right: 0; top: 178px;
    text-align: center;
    font-size: 13px;
    letter-spacing: 0.6px;
    line-height: 1.55;
    color: var(--muted);
  }
  .services .dot { color: var(--orange); }

  /* Front of card */
  .card--front {
    left: 618px;
    background: var(--paper);
    color: var(--ink);
  }
  .front-brand {
    position: absolute;
    left: 30px; top: 38px;
    display: flex;
    align-items: center;
    gap: 9px;
  }
  .card--front .brand-name { font-size: 25px; color: var(--ink); }
  .card--front .brand-mark { width: 11px; height: 11px; }
  .info-band {
    position: absolute;
    left: 0; top: 118px;
    width: 470px; height: 112px;
    background: var(--charcoal);
    border-radius: 0 56px 56px 0;
    color: #fff;
    display: grid;
    grid-template-columns: 150px 1fr;
    padding: 18px 30px 0 30px;
    column-gap: 16px;
  }
  .person-name {
    color: var(--orange);
    font-weight: 700;
    font-size: 19px;
    line-height: 1.1;
  }
  .person-title {
    font-size: 14px;
    margin-bottom: 10px;
  }
  .contact-line {
    display: flex;
    align-items: center;
    gap: 6px;
    font-size: 12.5px;
    line-height: 1.5;
  }
  .contact-line svg { width: 11px; height: 11px; flex: none; }
  .contact-col { padding-top: 30px; }
  .address {
    position: absolute;
    left: 30px; top: 252px;
    font-size: 13.5px;
    color: var(--ink);
  }
</style>
</head>
<body>

<section class="card card--back">
  <div class="back-brand">
    <span class="brand-mark"></span>
    <span class="brand-name">Northfield Builders Guild</span>
  </div>
  <p class="services">
    TECHNICAL ASSISTANCE <span class="dot">•</span> CONTRACTOR EDUCATION<br>
    SAFETY &amp; COMPLIANCE <span class="dot">•</span> CONTRACTOR DIRECTORY
  </p>
</section>

<section class="card card--front">
  <div class="front-brand">
    <span class="brand-mark"></span>
    <span class="brand-name">Northfield Builders Guild</span>
  </div>

  <div class="info-band">
    <div class="person">
      <p class="person-name">Daniel Reyes</p>
      <p class="person-title">President</p>
      <p class="contact-line">
        <svg viewBox="0 0 12 12"><path d="M2.5 1h2l1 3-1.3 1a6 6 0 0 0 2.8 2.8L8 6.5l3 1v2A1.5 1.5 0 0 1 9.5 11 8.5 8.5 0 0 1 1 2.5 1.5 1.5 0 0 1 2.5 1z" fill="var(--orange)"/></svg>
        (555) 231-4870
      </p>
      <p class="contact-line">
        <svg viewBox="0 0 12 12"><rect x="1" y="4" width="10" height="7" rx="1" fill="var(--orange)"/><rect x="3" y="1" width="6" height="3" fill="var(--orange)"/></svg>
        (555) 318-2046
      </p>
    </div>
    <div class="contact-col">
      <p class="contact-line">
        <svg viewBox="0 0 12 12"><rect x="1" y="2.5" width="10" height="7" fill="none" stroke="var(--orange)" stroke-width="1.2"/><path d="M1 2.5l5 4 5-4" fill="none" stroke="var(--orange)" stroke-width="1.2"/></svg>
        daniel@builderslinkguild.org
      </p>
      <p class="contact-line">
        <svg viewBox="0 0 12 12"><circle cx="6" cy="6" r="5" fill="none" stroke="var(--orange)" stroke-width="1.2"/><path d="M1 6h10M6 1c-2.5 3-2.5 7 0 10M6 1c2.5 3 2.5 7 0 10" fill="none" stroke="var(--orange)" stroke-width="1"/></svg>
        www.builderslinkguild.org
      </p>
    </div>
  </div>

  <p class="address">2400 Harbor Ridge Rd., Suite #210, Fairview, OR 97000</p>
</section>

</body>
</html>
```